Band and Coaching business card (creative industry)

My company The Fenwick Ensemble is the name of my band Soul outfit but is also a brand I use for my coaching business which is Performance coaching in the following areas: Corporate coaching, acting, vocals and dialect. The band plays for corporate events and private functions as well as local bar/restaurant/festivals.
Updates

Hi All

Please see updated info for the wording of the business card front and back.  This is ito then be followed with contact number, email and facebook link

first side should have:

JulieRose Brannigan
Creative Director
( followed by contact info as per previous)

Side 2:

The Fenwick Ensemble  - Band  
 Vocalist      I   Musician    I  Songwriter

The Fenwick Ensemble  - Studio
Performance Coaching  
Acting  I  Vocals  I Dialect  I Corporate Coaching

Industry/Entity Type

Events

Contact Information for Business Card

The Fenwick Ensemble (logo)
JulieRose Brannigan
Musician/Vocalist/Performance Coach
M: 0412 605 918
E: thefenwickensemble@mailbrook.net
W: www.friendspace.net/thefenwickensembleband

Font styles to use
Sans Serif

Requirements
Must have
• first side should have:

JulieRose Brannigan
Creative Director

Side 2:

The Fenwick Ensemble - Band
Vocalist I Musician I Songwriter

The Fenwick Ensemble - Studio
Performance Coaching
Acting I Vocals I Dialect I Corporate Coaching
Nice to have
• I like smaller business cards with curved edges.

some ideas for look in additional business cards attached.
Should not have
• music notes or anything specific to the field. Want to keep it funky and contemporary

```html
<!DOCTYPE html>
<html lang="en">
<head>
<meta charset="utf-8">
<title>JulieRose Brannigan – The Fenwick Ensemble</title>
<link rel="stylesheet" href="https://fonts.googleapis.com/css2?family=Yanone+Kaffeesatz:wght@400;500&family=Source+Sans+3:wght@400&display=swap">
<style>
  :root {
    --paper: #ffffff;
    --plum: #a93a8e;
    --rose: #e0408f;
    --orchid: #a2479c;
    --ink-contact: #a83b90;
  }
  html, body {
    margin: 0;
    padding: 0;
    overflow: hidden;
    background: var(--paper);
  }
  .card {
    position: relative;
    width: 1200px;
    height: 602px;
    background: var(--paper);
    overflow: hidden;
  }
  .card__band {
    position: absolute;
    inset: 0;
  }
  .holder-name {
    position: absolute;
    left: 84px;
    top: 126px;
    margin: 0;
    font-family: "Yanone Kaffeesatz", sans-serif;
    font-weight: 500;
    font-size: 84px;
    line-height: 1;
    color: var(--rose);
    white-space: nowrap;
  }
  .holder-role {
    position: absolute;
    right: 588px;
    top: 208px;
    margin: 0;
    font-family: "Source Sans 3", sans-serif;
    font-size: 25px;
    color: var(--orchid);
  }
  .contact {
    position: absolute;
    left: 86px;
    top: 314px;
    height: 186px;
    border-left: 4px solid var(--rose);
    margin: 0;
    padding: 0;
    list-style: none;
  }
  .contact__item {
    position: absolute;
    left: 30px;
    display: flex;
    align-items: center;
    gap: 10px;
    font-family: "Source Sans 3", sans-serif;
    font-size: 25px;
    color: var(--ink-contact);
    white-space: nowrap;
  }
  .contact__item--phone { top: 24px; }
  .contact__item--mail  { top: 76px; }
  .contact__item--web   { top: 129px; }
  .contact__icon {
    width: 24px;
    height: 24px;
    flex: none;
    fill: var(--ink-contact);
  }
  .brand-mark {
    position: absolute;
    left: 730px;
    top: 255px;
    width: 296px;
    height: 296px;
    border-radius: 50%;
    background: var(--rose);
    display: flex;
    align-items: center;
    justify-content: center;
    text-align: center;
  }
  .brand-mark__name {
    font-family: "Yanone Kaffeesatz", sans-serif;
    font-weight: 500;
    font-size: 50px;
    line-height: 0.95;
    color: var(--paper);
  }
</style>
</head>
<body>
  <div class="card">
    <svg class="card__band" width="1200" height="602" viewBox="0 0 1200 602" aria-hidden="true">
      <path d="M689,0 H1172 Q1200,0 1200,28 V574 Q1200,602 1172,602 H777 L990,136 Z" fill="var(--plum)"/>
    </svg>

    <h1 class="holder-name">JulieRose Brannigan</h1>
    <p class="holder-role">Creative Director</p>

    <ul class="contact">
      <li class="contact__item contact__item--phone">
        <svg class="contact__icon" viewBox="0 0 24 24" aria-hidden="true">
          <path d="M6.6 2.5c.6-.4 1.4-.2 1.7.4l2 3.6c.3.6.2 1.3-.4 1.7l-1.5 1c.7 1.9 2 3.6 3.7 4.8l1.2-1.3c.5-.5 1.2-.6 1.8-.2l3.4 2.3c.6.4.7 1.2.3 1.8l-1.4 2.1c-.6.9-1.7 1.3-2.8 1C8.900 18 4.800 12.400 4.400 6.200c-.1-1.100.4-2.100 1.300-2.700z"/>
        </svg>
        <span>:0412 605 918</span>
      </li>
      <li class="contact__item contact__item--mail">
        <svg class="contact__icon" viewBox="0 0 24 24" aria-hidden="true">
          <path d="M1 5h22v14H1z M2.5 6.5 12 13l9.5-6.5" fill="var(--ink-contact)"/>
          <path d="M2 6l10 7 10-7" fill="none" stroke="#fff" stroke-width="1.4"/>
        </svg>
        <span>:julierose@thefenwickensemble.net</span>
      </li>
      <li class="contact__item contact__item--web">
        <svg class="contact__icon" viewBox="0 0 24 24" aria-hidden="true">
          <rect x="5" y="4" width="14" height="16" rx="2"/>
        </svg>
        <span>:www.friendspace.net/thefenwickensembleband</span>
      </li>
    </ul>

    <div class="brand-mark">
      <span class="brand-mark__name">The Fenwick<br>Ensemble</span>
    </div>
  </div>
</body>
</html>
```